Book Title: “Faith: Road of Endless Grace” Please see the attachment “Text on the cover”.

Book Cover Design Instructions: This book is meant for people of all religions and nationalities. Therefore, on the cover, there should be no mosque or an object specific to any religion. The primary emphasis should be on the "unconditional love of God." Therefore, use universal symbols of love. The second priority themes could be Sufism, Peace, and self-improvement. Rest is your imagination. Please also see the attachment: 'Book description and author's Bio.'
This book has the potential to be a best seller. Please do a good job.
What Book Cover Formats are required: A designer should submit cover designs in three formats: (1) eBook, (2) Paperback, and (3) Hardback. These books will be published on Borvex QPL.
Format requirements for eBooks are available from: https://qpl.borvex.example/en_US/help/topic/R731928457.
You can find paperback and hardback cover measurements from: https://qpl.borvex.example/en_US/cover-calculator
• To complete the project, all three formats should be accepted by Borvex QPL.
• The book interior trim size is 6.14 X 9.21 inches.
• Interior Type: Premium color.
• No bleed.
• I do not upload barcode. So, the back cover should have room for Borvex to print the barcode.
• Number of pages 126.
Compensation for the designer: After selecting one designer, I will increase the amount by $200 on Artvelle to compensate for three deliverables.
Follow-up of the Project:
After the book is published, I may need minor revisions. For example, the number of pages may change. Therefore, I will need the same design in revised sizes. In that case, I will pay $25 for each revision. For example, if the number of pages changes, I will need a different spine for paperback and hardback, then I will pay the artist $25 + $25 = $50 for both designs.
List of Enclosers:
1. Text on the cover.
2. Book description and author's Bio for the back cover.
3. Later, I will upload my picture for the book's back cover.

Target Market(s)

Any adult

Industry/Entity Type

Any industry

Requirements
Must have
• Three Deliverables

```html
<!DOCTYPE html>
<html lang="en">
<head>
<meta charset="utf-8">
<title>Faith: Road of Endless Grace — Book Cover</title>
<link rel="stylesheet" href="https://fonts.googleapis.com/css2?family=Bebas+Neue&family=Montserrat:wght@500;600&display=swap">
<style>
  :root {
    --page: #ffffff;
    --cover-dark: #2e150a;
    --art-top: #8a4c1c;
    --art-orange: #e0861f;
    --art-gold: #f4b94a;
    --art-amber: #c8782a;
    --art-brown: #5a2a10;
    --title-white: #ffffff;
    --title-gold: #f8da85;
    --text-light: #ffffff;
    --rule: rgba(255, 220, 160, 0.35);
  }
  html, body {
    margin: 0;
    width: 1200px;
    height: 1200px;
    overflow: hidden;
    background: var(--page);
  }
  .cover {
    position: absolute;
    left: 293px;
    top: 140px;
    width: 614px;
    height: 920px;
    background: var(--cover-dark);
    overflow: hidden;
  }
  .cover-art {
    position: absolute;
    inset: 0;
    background: linear-gradient(180deg,
      var(--art-top) 0%,
      var(--art-orange) 10%,
      var(--art-gold) 30%,
      var(--art-amber) 44%,
      var(--art-brown) 57%,
      var(--cover-dark) 68%);
  }
  .tagline {
    position: absolute;
    left: 0;
    top: 36px;
    width: 100%;
    margin: 0;
    text-align: center;
    font-family: "Montserrat", sans-serif;
    font-weight: 500;
    color: var(--text-light);
    font-size: 35px;
    line-height: 40px;
    letter-spacing: 2px;
  }
  .title {
    position: absolute;
    left: 0;
    top: 0;
    width: 100%;
    margin: 0;
    font-family: "Bebas Neue", sans-serif;
    font-weight: 400;
    text-align: center;
  }
  .title-line {
    position: absolute;
    left: 0;
    width: 100%;
    display: block;
    line-height: 1;
    white-space: nowrap;
  }
  .title-line--lead {
    top: 340px;
    font-size: 212px;
    color: var(--title-white);
  }
  .title-line--mid {
    top: 507px;
    font-size: 212px;
    color: var(--title-gold);
  }
  .title-line--end {
    top: 686px;
    font-size: 112px;
    color: var(--title-gold);
  }
  .rule {
    position: absolute;
    left: 120px;
    width: 374px;
    height: 1px;
    background: linear-gradient(90deg, transparent, var(--rule), transparent);
  }
  .rule--upper { top: 802px; }
  .rule--lower { top: 880px; }
  .subtitle {
    position: absolute;
    left: 0;
    top: 810px;
    width: 100%;
    margin: 0;
    text-align: center;
    font-family: "Montserrat", sans-serif;
    font-weight: 500;
    font-size: 26px;
    line-height: 32px;
    letter-spacing: 1px;
    color: var(--text-light);
  }
  .author {
    position: absolute;
    left: 0;
    top: 886px;
    width: 100%;
    margin: 0;
    text-align: center;
    font-family: "Montserrat", sans-serif;
    font-weight: 500;
    font-size: 22px;
    line-height: 24px;
    letter-spacing: 1.5px;
    color: var(--text-light);
  }
</style>
</head>
<body>
  <main class="cover">
    <div class="cover-art" role="img" aria-label="Sunrise over a mountain and desert dunes in warm gold and brown tones"></div>
    <p class="tagline">UNCONDITIONAL<br>LOVE OF GOD</p>
    <h1 class="title">
      <span class="title-line title-line--lead">FAITH</span>
      <span class="title-line title-line--mid">ROAD OF</span>
      <span class="title-line title-line--end">ENDLESS GRACE</span>
    </h1>
    <div class="rule rule--upper"></div>
    <p class="subtitle">GUIDE TO CULTIVATING INNER<br>PEACE AND MINDFUL LIVING</p>
    <div class="rule rule--lower"></div>
    <p class="author">DR. NAVEEN ARSAL</p>
  </main>
</body>
</html>
```